20 year old business card needs re-design

We need to redesign our corporate business card look. We need something that appears more modern, eye catchy but professional.

Target Market(s)

manufacturing industry

Industry/Entity Type

Manufacturer

Contact Information for Business Card

One side can have the logo. Other side can have contact information.

Font styles to use
Serif

Colors
3277b5
33b8a4
ffffff

Requirements
Must have
• Eye catchy - need to standout from the crowd. company logo cannot change. Full name, job title, phone number and email address.
Should not have
• Fax, business address is not necessary.

```html
<!DOCTYPE html>
<html lang="en">
<head>
<meta charset="utf-8">
<title>Norvale Industrial – Business Card</title>
<link rel="stylesheet" href="https://fonts.googleapis.com/css2?family=Libre+Baskerville:wght@400;700&family=Roboto:wght@400;500&display=swap">
<style>
  :root {
    --stage: #2b2b2b;
    --card: #f4f4f4;
    --blue: #3277b5;
    --teal: #33b8a4;
    --ink: #1e1e1e;
    --grey: #555555;
    --white: #ffffff;
  }
  * { box-sizing: border-box; margin: 0; padding: 0; }
  html, body { width: 1200px; height: 834px; overflow: hidden; }
  body {
    background: var(--stage);
    font-family: "Roboto", Arial, sans-serif;
    display: flex;
    align-items: center;
    justify-content: center;
    gap: 60px;
  }
  .card {
    position: relative;
    width: 520px;
    height: 297px;
    background: var(--card);
    box-shadow: 0 10px 30px rgba(0,0,0,0.45);
    overflow: hidden;
  }
  .wordmark {
    position: absolute;
    left: 0; right: 0;
    display: flex;
    align-items: center;
    justify-content: center;
    gap: 12px;
  }
  .wordmark__square {
    width: 26px; height: 26px;
    background: var(--blue);
  }
  .wordmark__name {
    font-family: "Libre Baskerville", Georgia, serif;
    font-weight: 700;
    font-size: 30px;
    color: var(--ink);
    letter-spacing: 0.5px;
  }
  /* front */
  .card--front .wordmark { top: 92px; }
  .front-band {
    position: absolute;
    left: 0; right: 0;
    top: 196px;
    height: 66px;
    background: var(--blue);
    display: flex;
    align-items: center;
    justify-content: center;
  }
  .tagline {
    color: var(--white);
    font-size: 13px;
    line-height: 1.4;
    text-align: center;
  }
  /* back */
  .card--back .wordmark { top: 58px; }
  .identity {
    position: absolute;
    top: 130px; left: 0; right: 0;
    text-align: center;
    font-family: "Libre Baskerville", Georgia, serif;
    font-weight: 700;
    font-size: 16px;
    color: var(--grey);
  }
  .identity__title {
    font-family: "Roboto", Arial, sans-serif;
    font-weight: 400;
    color: var(--teal);
  }
  .contact {
    position: absolute;
    top: 166px; left: 0; right: 0;
    list-style: none;
    text-align: center;
    font-size: 13px;
    line-height: 1.55;
    color: var(--grey);
  }
  .contact__label {
    color: var(--blue);
    font-weight: 500;
    margin-right: 4px;
  }
  .back-band {
    position: absolute;
    left: 0; right: 0; bottom: 0;
    height: 16px;
    background: var(--blue);
  }
</style>
</head>
<body>
  <section class="card card--front">
    <div class="wordmark">
      <span class="wordmark__square"></span>
      <span class="wordmark__name">Norvale Industrial</span>
    </div>
    <div class="front-band">
      <p class="tagline">International Manufacturing Solutions for OEM<br>customers in North America</p>
    </div>
  </section>

  <section class="card card--back">
    <div class="wordmark">
      <span class="wordmark__square"></span>
      <span class="wordmark__name">Norvale Industrial</span>
    </div>
    <p class="identity">Dan Keller - <span class="identity__title">President</span></p>
    <ul class="contact">
      <li><span class="contact__label">P.</span>555-014-2200 x104</li>
      <li><span class="contact__label">E.</span>dan@norvaleindustrial.com</li>
      <li><span class="contact__label">W.</span>www.norvaleindustrial.com</li>
    </ul>
    <div class="back-band"></div>
  </section>
</body>
</html>
```